Website art for a private investigator.

The purposed graphic is for a business website ( brellwick.com ). The business name is “Harrowgate & Associates ltd.” This firm is a private investigation agency. The purposed graphic will be placed in the upper most main area of the main page of the website. If you look at the website now there is no graphic.

I have an idea of what I am looking for. I imagine a graphic depicting a contemporary private investigator walking through a dark alley searching for some unknown item. This is symbolic of private investigators hired to find information for people who their selfs do not have the know how nor could they handle the complexity and high stress environment. When I say contemporary I am referring to todays private investigators typically highly educated and well dressed.

Target Market(s)

People who need a private investigator

Industry/Entity Type

Business

Requirements
Must have
• match website; I have an idea of what I am looking for. I imagine a graphic depicting a contemporary private investigator walking through a dark alley searching for some unknown item. This is symbolic of private investigators hired to find information for people who their selfs do not have the know how nor could they handle the complexity and high stress environment. When I say contemporary I am referring to todays private investigators typically highly educated and well dressed.
Should not have
• Everyone please understand, I am not looking for a new website. I am only looking for the image. If you have submitted a design and its displayed on another website other than mine. I will not select your design. I am sorry for being harsh, but I asked for the image to match my website.

```html
<!DOCTYPE html>
<html lang="en">
<head>
<meta charset="utf-8">
<title>Harrowgate &amp; Associates ltd.</title>
<link rel="stylesheet" href="https://fonts.googleapis.com/css2?family=Raleway:wght@300;400;500;700&family=Teko:wght@400&family=Arimo:wght@400&display=swap">
<style>
:root{
  --red:#c11b2c;
  --red-light:#d83a49;
  --ink:#222;
  --muted:#6d6d6d;
  --header-grey:#efefef;
  --chevron-grey:#d9d9d9;
  --dark:#0b0b0b;
  --line:#3a3a3a;
  --white:#fff;
}
*{box-sizing:border-box;margin:0;padding:0}
html,body{width:699px;height:1200px;overflow:hidden;background:var(--white)}
body{position:relative;font-family:"Arimo",Arial,sans-serif;color:var(--ink)}

.site-header{position:absolute;left:0;top:0;width:699px;height:61px;background:var(--header-grey)}
.site-header .band{position:absolute;inset:0}
.brand{position:absolute;left:58px;top:15px;display:flex;align-items:center;gap:7px}
.brand-dot{width:22px;height:22px;border-radius:50%;background:var(--red)}
.brand-name{font-family:"Raleway",sans-serif;font-weight:700;font-size:15px;color:var(--red);line-height:1.05;width:170px}
.search{position:absolute;left:523px;top:9px;width:118px;height:17px;background:var(--red-light)}
.search svg{position:absolute;right:6px;top:3px}
.nav-item{position:absolute;top:38px;font-family:"Raleway",sans-serif;font-weight:500;font-size:8.3px;color:var(--white);letter-spacing:.3px;white-space:nowrap}
.nav-main{left:332px}.nav-invest{left:390px}.nav-news{left:557px}.nav-fees{left:618px}

.hero{position:absolute;left:0;top:61px;width:699px;height:264px;background:#000}
.hero-photo{position:absolute;left:58px;top:0;width:583px;height:264px;
  background:
    radial-gradient(ellipse 70px 40px at 320px 18px,rgba(235,235,235,.85),rgba(235,235,235,0)),
    radial-gradient(ellipse 60px 120px at 320px 110px,rgba(150,150,150,.55),rgba(150,150,150,0)),
    radial-gradient(ellipse 120px 150px at 410px 170px,rgba(110,110,110,.55),rgba(110,110,110,0)),
    radial-gradient(ellipse 50px 40px at 250px 160px,rgba(210,210,210,.6),rgba(210,210,210,0)),
    linear-gradient(180deg,rgba(0,0,0,0) 60%,rgba(70,70,70,.5) 85%,rgba(20,20,20,.8)),
    linear-gradient(90deg,#141414 0%,#2e2e2e 18%,#3a3a3a 35%,#5e5e5e 50%,#3c3c3c 62%,#2a2a2a 80%,#1a1a1a 100%)}

.section-title{font-family:"Raleway",sans-serif;font-weight:300;font-size:18px;letter-spacing:.5px;text-align:center;text-transform:uppercase}
.section-title strong{font-weight:500}

.services{position:absolute;left:0;top:325px;width:699px;height:249px}
.services .section-title{position:absolute;top:30px;width:100%}
.services .intro{position:absolute;top:54px;left:94px;width:511px;text-align:center;font-size:8.9px;line-height:14.5px;color:#333}
.service{position:absolute;top:110px;width:190px}
.service .disc{position:absolute;left:0;top:0;width:87px;height:87px;border-radius:50%;border:1px solid #bbb;padding:4px;background:var(--white)}
.service .disc div{width:100%;height:100%;border-radius:50%}
.service h3{position:absolute;left:96px;font-family:"Teko",sans-serif;font-weight:400;font-size:19px;line-height:14px;color:var(--red)}
.service p{position:absolute;left:97px;width:88px;font-size:8.3px;line-height:14.5px;color:var(--muted)}
.s1{left:59px}.s2{left:258px}.s3{left:457px}
.s1 h3{top:7px}.s1 p{top:45px}
.s2 h3{top:13px}.s2 p{top:51px}
.s3 h3{top:5px}.s3 p{top:43px}

.about{position:absolute;left:0;top:574px;width:699px;height:194px;
  background:radial-gradient(circle at 20% 30%,#fff 0,#f4f4f4 25%,transparent 40%),linear-gradient(180deg,#e9e9e9,#f6f6f6 60%,#fbfbfb)}
.about .section-title{position:absolute;top:44px;width:100%}
.about p{position:absolute;top:74px;left:89px;width:521px;text-align:center;font-size:8.5px;line-height:14.6px;color:#444}
.read-more{position:absolute;top:151px;width:100%;text-align:center;font-size:10.5px;color:#111}

.contact{position:absolute;left:0;top:768px;width:699px;height:325px;
  background:radial-gradient(ellipse at 45% 40%,#2a2a2a 0%,#141414 40%,var(--dark) 80%)}
.contact .section-title{position:absolute;top:35px;width:100%;color:var(--white)}
.field{position:absolute;border:1px solid var(--line);font-size:9px;color:#aaa;padding:10px 8px}
.f-name{left:58px;top:83px;width:158px;height:31px}
.f-mail{left:228px;top:83px;width:155px;height:31px}
.f-msg{left:58px;top:124px;width:325px;height:99px}
.send{position:absolute;left:58px;top:241px;width:325px;height:32px;background:var(--red);color:var(--white);font-family:"Raleway",sans-serif;font-size:10.5px;text-align:center;line-height:32px}
.contact .lead{position:absolute;left:398px;top:92px;width:248px;font-size:8.8px;line-height:14px;color:#ddd}
.office-label{position:absolute;left:398px;top:124px;font-size:10px;color:var(--red);letter-spacing:.3px}
.info-row{position:absolute;left:399px;display:flex;align-items:flex-start;gap:14px;color:#eee;font-size:8.8px;line-height:12.8px}
.info-row svg{flex:none}
.r-addr{top:141px}.r-mail{top:219px}.r-tel{top:256px}
.r-mail span,.r-tel span{padding-top:4px}

.site-footer{position:absolute;left:0;top:1093px;width:699px;height:107px;text-align:center}
.site-footer .rights{position:absolute;top:34px;width:100%;font-size:9.8px;color:#111}
.site-footer .copy{position:absolute;top:55px;width:100%;font-size:8.6px;color:#333;letter-spacing:.3px}
</style>
</head>
<body>

<header class="site-header">
  <svg class="band" width="699" height="61" viewBox="0 0 699 61" aria-hidden="true">
    <polygon points="244,0 268,0 290,30 268,61 244,61 266,30" fill="#d9d9d9"/>
    <polygon points="312,0 699,0 699,61 312,61 290,30" fill="#c11b2c"/>
  </svg>
  <div class="brand">
    <span class="brand-dot"></span>
    <span class="brand-name">Harrowgate &amp;<br>Associates ltd.</span>
  </div>
  <div class="search">
    <svg width="11" height="11" viewBox="0 0 11 11"><circle cx="4.5" cy="4.5" r="3.4" fill="none" stroke="#fff" stroke-width="1.3"/><line x1="7" y1="7" x2="10" y2="10" stroke="#fff" stroke-width="1.4"/></svg>
  </div>
  <nav>
    <span class="nav-item nav-main">MAIN</span>
    <span class="nav-item nav-invest">INVESTIGATION &amp; ANNALYSIS</span>
    <span class="nav-item nav-news">NEWS</span>
    <span class="nav-item nav-fees">FEES</span>
  </nav>
</header>

<section class="hero">
  <div class="hero-photo" role="img" aria-label="Black and white photo of a well-dressed private investigator crouching in a dark narrow alley under a distant street light, holding up an evidence bag with a camera around his neck"></div>
</section>

<section class="services">
  <h2 class="section-title">Harrowgate <strong>Services</strong></h2>
  <p class="intro">Sed ut perspiciatis unde omnis iste natus error sit voluptatem accusantium doloremque laudantium,totam rem aperiam, eaque ipsa quae ab illo inventore veritatis et quasi architecto beatae vitae dicta.</p>

  <div class="service s1">
    <div class="disc"><div role="img" aria-label="Photo of two hands in a handshake" style="background:radial-gradient(circle at 50% 55%,#c98f7a,#7a4b3c 60%,#2b1f1a)"></div></div>
    <h3>Criminal<br>Defense</h3>
    <p>Sed ut perspiciatis unde omnis iste natus error sit voluptatem accusantium.</p>
  </div>
  <div class="service s2">
    <div class="disc"><div role="img" aria-label="Photo of a magnifying glass over a document" style="background:linear-gradient(160deg,#2a1a1a 0%,#5a3a35 35%,#e8e6e2 60%,#f4f3f1)"></div></div>
    <h3>Legal<br>Investigation</h3>
    <p>Sed ut perspiciatis unde omnis iste natus error sit voluptatem accusantium .</p>
  </div>
  <div class="service s3">
    <div class="disc"><div role="img" aria-label="Photo of a photographer with a camera in a dark room" style="background:radial-gradient(circle at 40% 40%,#9a9a9a,#3a3a3a 45%,#0c0c0c)"></div></div>
    <h3>Forensic<br>Photography</h3>
    <p>Sed ut perspiciatis unde omnis iste natus error sit voluptatem accusantium.</p>
  </div>
</section>

<section class="about">
  <h2 class="section-title">What we do <strong>Harrowgate</strong></h2>
  <p>Lorem Ipsum is simply dummy text of the printing and typesetting industry. Lorem Ipsum has been the industry's standard dummy text ever since the 1500s, when an unknown printer took a galley of type and scrambled it to make a type specimen book. It has survived not only five centuries, but also the leap into electronic typesetting, remaining essentially unchanged. It was popularised in the 1960s with the including versions of Lorem Ipsum.</p>
  <div class="read-more">Read More &gt;&gt;</div>
</section>

<section class="contact">
  <h2 class="section-title">Contact <strong>Form</strong></h2>
  <div class="field f-name">Your name</div>
  <div class="field f-mail">Your e-mail</div>
  <div class="field f-msg">Your message</div>
  <div class="send">SEND MESSAGE</div>

  <p class="lead">Sed ut perspiciatis unde omnis iste natus error sit voluptatem accusantium doloremque laudantium,totam rem</p>
  <div class="office-label">OUR OFFICE</div>

  <div class="info-row r-addr">
    <svg width="22" height="22" viewBox="0 0 22 22"><circle cx="11" cy="11" r="10" fill="none" stroke="#ddd" stroke-width="1.2"/><path d="M11 5.5a3.3 3.3 0 0 0-3.3 3.3c0 2.5 3.3 6.2 3.3 6.2s3.3-3.7 3.3-6.2A3.3 3.3 0 0 0 11 5.5z" fill="#ddd"/><circle cx="11" cy="8.8" r="1.1" fill="#111"/></svg>
    <span>P.O. Box 412<br>Aldmere, Ohio 45901<br><span style="display:block;margin-top:3px">4th Floor, 118 Calder Street,<br>London, UK,<br>W1C 2LT</span></span>
  </div>
  <div class="info-row r-mail">
    <svg width="22" height="22" viewBox="0 0 22 22"><circle cx="11" cy="11" r="10" fill="none" stroke="#ddd" stroke-width="1.2"/><rect x="6" y="7.5" width="10" height="7" fill="none" stroke="#ddd" stroke-width="1"/><polyline points="6,7.5 11,11.5 16,7.5" fill="none" stroke="#ddd" stroke-width="1"/></svg>
    <span>info@brellwick.com</span>
  </div>
  <div class="info-row r-tel">
    <svg width="22" height="22" viewBox="0 0 22 22"><circle cx="11" cy="11" r="10" fill="none" stroke="#ddd" stroke-width="1.2"/><path d="M8 6l2 2.4-1.2 1.3c.6 1.4 1.7 2.5 3 3.1l1.3-1.2L15.5 13.6 14.4 15.6C10.8 15.4 6.6 11.2 6.4 7.6z" fill="#ddd"/></svg>
    <span>(740) 555-0147</span>
  </div>
</section>

<footer class="site-footer">
  <p class="rights">© 2014-2015 Harrowgate &amp; Associates ltd. All rights resesrved.</p>
  <p class="copy">Copyright © 2015-2015 . All Rights Reserved.</p>
</footer>

</body>
</html>
```